Telecommunications/Power civil contractor needs business card design

Were a new telecommunications/power underground civil contractor that is looking for a new business card design. Our company colours are silver or grey and orange. Feel free to use the white background logo or the black background logo.

Target Market(s)

Local contractors, utility companies, private sector mining/energy companies, developers.

Industry/Entity Type

Telecommunications

Contact Information for Business Card

Each card will need the following info:
Persons name:
Title:
E-mail:
Phone number:
Shop Address:
Mailing Address:

Requirements
Must have
• Each card will need the following info:
• Persons name:
• Title:
• E-mail:
• Phone number:
• Shop Address:
• Mailing Address:

```html
<!DOCTYPE html>
<html lang="en">
<head>
<meta charset="utf-8">
<title>Bore Line Contracting – Business Card</title>
<link rel="stylesheet" href="https://fonts.googleapis.com/css2?family=Russo+One&family=Montserrat:wght@400;500;600&display=swap">
<style>
  :root{
    --stage:#dcd7cf;
    --ink:#0b0b0b;
    --ink-soft:#2a2a2a;
    --steel-light:#9b9b9b;
    --steel:#6f6f6f;
    --steel-dark:#4a4a4a;
    --orange:#f2622a;
    --white:#f4f4f4;
    --muted:#c9c9c9;
  }
  *{box-sizing:border-box;margin:0;padding:0}
  html,body{width:1200px;height:1022px;overflow:hidden}
  body{background:var(--stage);font-family:"Montserrat",Arial,sans-serif;position:relative}
  .card{position:absolute;left:230px;width:740px;height:423px;border-radius:22px;overflow:hidden;box-shadow:0 10px 26px rgba(0,0,0,.25)}
  .card--front{top:70px}
  .card--back{top:529px}
  .card svg.card-art{position:absolute;inset:0;width:100%;height:100%}
  .brand{position:absolute;left:42px;top:92px}
  .brand__name{font-family:"Russo One",Arial,sans-serif;font-size:58px;line-height:1;color:var(--orange);letter-spacing:1px}
  .brand__sub{font-family:"Russo One",Arial,sans-serif;font-size:27px;color:var(--white);letter-spacing:1px;margin-top:4px}
  .person{position:absolute;left:42px;top:212px}
  .person__name{font-size:27px;font-weight:500;color:var(--orange);letter-spacing:1px}
  .person__title{font-size:16px;color:var(--muted);margin-top:2px}
  .address{position:absolute;left:42px;top:292px;font-size:17px;line-height:24px;color:var(--white)}
  .address p + p{margin-top:8px}
  .contact{position:absolute;right:40px;top:210px;text-align:right;font-size:16px;line-height:25px;color:var(--white)}
  .contact__gap{height:14px}
  .contact-icons{position:absolute;right:40px;top:178px;display:flex;gap:10px}
  .contact-icons svg{width:16px;height:16px}
  .logo-mark{position:absolute;display:flex;align-items:center;justify-content:center;border-radius:50%;background:var(--ink);border:5px solid var(--steel-light)}
  .logo-mark span{font-family:"Russo One",Arial,sans-serif;color:var(--orange);text-align:center;line-height:1}
  .card--front .logo-mark{left:470px;top:28px;width:150px;height:150px}
  .card--front .logo-mark span{font-size:24px}
  .card--back .logo-mark{left:250px;top:72px;width:240px;height:240px}
  .card--back .logo-mark span{font-size:40px}
  .back-tagline{position:absolute;left:0;right:0;top:340px;text-align:center;font-family:"Russo One",Arial,sans-serif;font-size:22px;color:var(--white);letter-spacing:3px}
</style>
</head>
<body>

<section class="card card--front" aria-label="Business card front">
  <svg class="card-art" viewBox="0 0 740 423" aria-hidden="true">
    <defs>
      <linearGradient id="steelFront" x1="0" y1="0" x2="1" y2="1">
        <stop offset="0" stop-color="#8c8c8c"/>
        <stop offset=".5" stop-color="#6a6a6a"/>
        <stop offset="1" stop-color="#4c4c4c"/>
      </linearGradient>
      <linearGradient id="inkFront" x1="0" y1="0" x2="1" y2="0">
        <stop offset="0" stop-color="#050505"/>
        <stop offset="1" stop-color="#262626"/>
      </linearGradient>
    </defs>
    <rect width="740" height="423" fill="url(#inkFront)"/>
    <path d="M545 0 C 420 150, 560 300, 420 423 L740 423 L740 0 Z" fill="url(#steelFront)"/>
    <path d="M545 0 C 420 150, 560 300, 420 423" fill="none" stroke="#f2622a" stroke-width="6"/>
    <rect x="640" y="0" width="100" height="14" fill="#f2622a"/>
    <path d="M0 423 L60 423 L0 380 Z" fill="#f2622a"/>
  </svg>

  <div class="logo-mark"><span>BORE<br>LINE</span></div>

  <div class="brand">
    <div class="brand__name">BORE LINE</div>
    <div class="brand__sub">CONTRACTING INC</div>
  </div>

  <div class="person">
    <div class="person__name">MARCUS HALE</div>
    <div class="person__title">Director</div>
  </div>

  <div class="address">
    <p>48 Quarry Lane<br>Millbrook, NY 12545</p>
    <p>PO BOX 3150<br>RESEDA, CA 91335</p>
  </div>

  <div class="contact-icons" aria-hidden="true">
    <svg viewBox="0 0 16 16"><rect x="4" y="1" width="8" height="14" rx="2" fill="none" stroke="#f2622a" stroke-width="1.6"/></svg>
    <svg viewBox="0 0 16 16"><path d="M4 2 L7 5 L5.5 7 C6.5 9 7.5 10 9.5 11 L11 9.5 L14 12.5 L12 14.5 C7 14 2 9 1.5 4 Z" fill="#f2622a"/></svg>
    <svg viewBox="0 0 16 16"><rect x="1.5" y="3.5" width="13" height="9" fill="none" stroke="#f2622a" stroke-width="1.6"/><path d="M1.5 3.5 L8 9 L14.5 3.5" fill="none" stroke="#f2622a" stroke-width="1.6"/></svg>
    <svg viewBox="0 0 16 16"><circle cx="8" cy="8" r="6.3" fill="none" stroke="#f2622a" stroke-width="1.6"/><path d="M1.7 8 H14.3 M8 1.7 C5 5, 5 11, 8 14.3 M8 1.7 C11 5, 11 11, 8 14.3" fill="none" stroke="#f2622a" stroke-width="1.2"/></svg>
  </div>

  <div class="contact">
    <div>+330 2418-5032</div>
    <div>+330 4371-6620</div>
    <div class="contact__gap"></div>
    <div>info@borelinecontracting.com</div>
    <div>www.borelinecontracting.com</div>
  </div>
</section>

<section class="card card--back" aria-label="Business card back">
  <svg class="card-art" viewBox="0 0 740 423" aria-hidden="true">
    <defs>
      <linearGradient id="steelBack" x1="0" y1="0" x2="1" y2="1">
        <stop offset="0" stop-color="#8c8c8c"/>
        <stop offset="1" stop-color="#4c4c4c"/>
      </linearGradient>
    </defs>
    <rect width="740" height="423" fill="#0b0b0b"/>
    <path d="M0 0 L230 0 C 330 120, 180 300, 300 423 L0 423 Z" fill="url(#steelBack)"/>
    <path d="M230 0 C 330 120, 180 300, 300 423" fill="none" stroke="#f2622a" stroke-width="6"/>
    <rect x="0" y="409" width="120" height="14" fill="#f2622a"/>
    <path d="M740 0 L680 0 L740 43 Z" fill="#f2622a"/>
  </svg>
  <div class="logo-mark"><span>BORE<br>LINE</span></div>
  <div class="back-tagline">CONTRACTING INC</div>
</section>

</body>
</html>
```